Coastline Premier Retreats Business Card Design

Design a business card for Coastline Premier Retreats. Look at the website for colors and reference. Card should have logo, name, title, office number, mobile number, email, URL and a tagline like, "Luxury Hotel & Resort Email Marketing" (This might change).

https://www.coastlinepremierretreats.example

The rest I will leave up to your imagination.

Contact Information for Business Card

Logo, name, title, office number, mobile number, email, URL and a tagline like, "Luxury Hotel & Resort Email Marketing" (This might change).

```html
<!DOCTYPE html>
<html lang="en">
<head>
<meta charset="utf-8">
<title>Coastline Premier Retreats – Business Card</title>
<link rel="stylesheet" href="https://fonts.googleapis.com/css2?family=Montserrat:wght@400;500;600;700;800&display=swap">
<style>
  :root {
    --bg: #2b2b2c;
    --card: #1b1b1c;
    --orange: #f07214;
    --white: #ffffff;
    --mark-grey: #4d4d50;
  }
  * { margin: 0; padding: 0; box-sizing: border-box; }
  html, body { width: 1200px; height: 1200px; overflow: hidden; }
  body {
    background: var(--bg);
    font-family: "Montserrat", sans-serif;
    display: flex;
    align-items: center;
    justify-content: center;
    gap: 70px;
  }
  .card {
    position: relative;
    width: 440px;
    height: 770px;
    background: var(--card);
    border-radius: 24px;
    overflow: hidden;
  }

  /* Front */
  .brand {
    position: absolute;
    top: 120px;
    left: 60px;
    right: 50px;
    display: flex;
    align-items: center;
    gap: 16px;
  }
  .brand-square {
    flex: none;
    width: 22px;
    height: 22px;
    background: var(--orange);
  }
  .brand-name {
    color: var(--white);
    font-weight: 700;
    font-size: 30px;
    line-height: 1.1;
    text-transform: uppercase;
    letter-spacing: 0.5px;
  }
  .accent-bar {
    position: absolute;
    left: 22px;
    top: 462px;
    width: 22px;
    height: 56px;
    background: var(--orange);
  }
  .person {
    position: absolute;
    left: 70px;
    top: 462px;
  }
  .person-name {
    color: var(--orange);
    font-weight: 700;
    font-size: 34px;
    letter-spacing: 1.5px;
    text-transform: uppercase;
    line-height: 1;
  }
  .person-title {
    color: var(--white);
    font-weight: 500;
    font-size: 17px;
    letter-spacing: 0.6px;
    margin-top: 8px;
  }
  .contacts {
    position: absolute;
    left: 40px;
    top: 590px;
    list-style: none;
    color: var(--white);
    font-size: 17px;
    font-weight: 500;
    letter-spacing: 0.4px;
  }
  .contacts li {
    display: flex;
    align-items: center;
    gap: 12px;
    margin-bottom: 14px;
    white-space: nowrap;
  }
  .contacts svg { flex: none; width: 16px; height: 16px; }
  .contact-label {
    color: var(--orange);
    font-size: 12px;
    margin-left: 6px;
  }
  .contacts .email { font-size: 14px; }

  /* Back */
  .back-mark {
    position: absolute;
    left: 150px;
    top: 80px;
    height: 610px;
    writing-mode: vertical-rl;
    transform: rotate(180deg);
    color: var(--mark-grey);
    font-weight: 800;
    font-size: 62px;
    line-height: 1.05;
    text-transform: uppercase;
    letter-spacing: 2px;
    text-align: center;
  }
  .tagline {
    position: absolute;
    right: 52px;
    bottom: 90px;
    writing-mode: vertical-rl;
    transform: rotate(180deg);
    color: var(--orange);
    font-size: 22px;
    font-weight: 500;
    letter-spacing: 0.3px;
  }
</style>
</head>
<body>
  <section class="card card-front">
    <div class="brand">
      <span class="brand-square"></span>
      <span class="brand-name">Coastline Premier Retreats</span>
    </div>

    <span class="accent-bar"></span>
    <div class="person">
      <h1 class="person-name">Daniel Hart</h1>
      <p class="person-title">Managing Director</p>
    </div>

    <ul class="contacts">
      <li>
        <svg viewBox="0 0 16 16" aria-hidden="true"><rect x="4" y="1" width="8" height="14" rx="1.5" fill="none" stroke="#f07214" stroke-width="1.4"/><circle cx="8" cy="12.5" r="0.9" fill="#f07214"/></svg>
        <span>555.014.2287<span class="contact-label">(Mobile)</span></span>
      </li>
      <li>
        <svg viewBox="0 0 16 16" aria-hidden="true"><path d="M2 6c0-2 2.5-3 6-3s6 1 6 3v1.5h-3V6H5v1.5H2z" fill="#f07214"/><rect x="3.5" y="8.5" width="9" height="5.5" rx="1" fill="#f07214"/></svg>
        <span>555.019.3300<span class="contact-label">(Office)</span></span>
      </li>
      <li class="email">
        <svg viewBox="0 0 16 16" aria-hidden="true"><rect x="1.5" y="4" width="13" height="9" rx="1" fill="#f07214"/><path d="M1.5 4.5 8 9.5l6.5-5" fill="none" stroke="#1b1b1c" stroke-width="1.2"/></svg>
        <span>dhart@coastlinepremierretreats.example</span>
      </li>
    </ul>
  </section>

  <section class="card card-back">
    <div class="back-mark">Coastline Premier Retreats</div>
    <p class="tagline">Luxury Hotel &amp; Resort Email Marketing</p>
  </section>
</body>
</html>
```